corvale institute of business and technology web site

I need web site for the institute which focus on business courses and computer course it is also for vocation train for employment It is also carear development and advancement .It should have links to online study resource which free
Industry/Entity Type
Business
Number of Pages Required
1 page
Look and feel
Each slider illustrates characteristics of the customer's brand and the style your logo design should communicate.

```html
<!DOCTYPE html>
<html lang="en">
<head>
<meta charset="utf-8">
<title>Corvale Institute of Business and Technology</title>
<link href="https://fonts.googleapis.com/css2?family=Open+Sans:ital,wght@0,400;0,600;0,700;0,800;1,300;1,400&family=Lora:ital@1&display=swap" rel="stylesheet">
<style>
:root{
  --navy:#1b3b86;
  --navy-deep:#152c63;
  --blue:#2b63c4;
  --blue-light:#3f86e0;
  --green:#6cb33e;
  --orange:#f39c1f;
  --ink:#333;
  --muted:#777;
  --line:#dedede;
  --pale:#f4f4f4;
  --white:#fff;
}
*{box-sizing:border-box;margin:0;padding:0}
html,body{width:1200px;height:4064px;overflow:hidden}
body{font-family:"Open Sans",Arial,sans-serif;color:var(--ink);background:var(--white);position:relative}
.section-title{text-align:center;font-weight:700;font-size:24px;color:var(--ink);text-transform:uppercase;letter-spacing:.5px}
.section-title::after{content:"";display:block;width:90px;height:3px;background:var(--green);margin:14px auto 0}

/* top bar */
.topbar{position:absolute;top:0;left:0;width:1200px;height:32px;background:var(--navy-deep);color:#cfd8ee;font-size:13px;display:flex;align-items:center;justify-content:space-between;padding:0 40px}
.topbar .phone{display:flex;align-items:center;gap:8px}
.topbar .dots{display:flex;gap:6px}
.topbar .dots span{width:18px;height:18px;border-radius:50%;border:1px solid #9fb0d6}

/* hero */
.hero{position:absolute;top:32px;left:0;width:1200px;height:830px;overflow:hidden}
.hero-photo{position:absolute;inset:0;background:linear-gradient(180deg,#d9d9d6 0%,#ecebe7 45%,#c9c4bb 75%,#8c8274 100%)}
.nav{position:absolute;top:0;left:0;width:1200px;height:84px;background:linear-gradient(180deg,var(--blue) 0%,var(--navy) 100%);display:flex;justify-content:space-between;align-items:center;padding:0 200px}
.nav ul{list-style:none;display:flex;gap:42px}
.nav a{color:var(--white);font-size:15px;font-weight:600;text-decoration:none;text-transform:uppercase}
.brand{position:absolute;left:470px;top:0;width:260px;height:200px;background:var(--white);border-radius:0 0 40px 40px;box-shadow:0 6px 14px rgba(0,0,0,.25);text-align:center;padding-top:20px}
.brand .mark{width:62px;height:62px;border-radius:50%;background:var(--navy);margin:0 auto 12px}
.brand .name{font-size:38px;font-weight:800;color:var(--navy);letter-spacing:1px}
.brand .tag{font-size:10px;font-weight:700;color:var(--navy);letter-spacing:.3px;margin-top:2px}
.hero-copy{position:absolute;top:320px;width:1200px;text-align:center;color:var(--white);text-shadow:0 2px 6px rgba(0,0,0,.45)}
.hero-copy h1{font-size:56px;font-weight:400}
.hero-copy p{font-size:26px;margin-top:4px}
.hero .btn{position:absolute;left:535px;top:700px;width:130px;height:38px;border-radius:20px;background:var(--blue);color:var(--white);font-size:13px;font-weight:700;display:flex;align-items:center;justify-content:center}
.hero .divider{position:absolute;left:0;bottom:0}

/* programs */
.programs{position:absolute;top:910px;left:0;width:1200px}
.program-list{display:flex;gap:38px;justify-content:center;margin-top:60px}
.program{width:150px;height:300px;border-radius:75px 75px 30px 30px;background:linear-gradient(180deg,var(--blue-light),var(--navy));position:relative;text-align:center;color:var(--white);padding:150px 12px 0;box-shadow:0 6px 10px rgba(0,0,0,.2)}
.program.active .icon{background:var(--green)}
.program .icon{position:absolute;top:20px;left:25px;width:100px;height:100px;border-radius:50%;background:var(--blue);border:6px solid var(--white);display:flex;align-items:center;justify-content:center}
.program h3{font-size:13px;font-weight:700;line-height:1.35}

/* about */
.about{position:absolute;top:1390px;left:0;width:1200px;padding:0 75px}
.about .intro{margin-top:42px;font-size:13px;line-height:1.75;color:var(--muted);text-align:left}
.about-boxes{display:flex;gap:28px;margin-top:42px}
.about-box{flex:1;border:1px solid var(--line);padding:20px 24px;height:170px}
.about-box h4{display:flex;align-items:center;gap:12px;font-size:20px;font-weight:600;color:var(--ink)}
.about-box p{font-size:12.5px;color:var(--muted);line-height:1.7;margin-top:14px}

/* why */
.why{position:absolute;top:1860px;left:0;width:1200px}
.why-grid{position:absolute;top:100px;left:80px;width:520px;display:grid;grid-template-columns:1fr 1fr;gap:30px 40px}
.why-item .num{font-size:64px;font-style:italic;font-weight:300;color:#cfcfcf;line-height:1}
.why-item h4{font-size:17px;font-weight:600;margin-top:6px;line-height:1.3}
.why-item p{font-size:12px;color:var(--muted);line-height:1.7;margin-top:10px}
.why-photo{position:absolute;top:100px;left:615px;width:565px;height:540px;background:linear-gradient(135deg,#e8ebee,#c3c9cf 60%,#8d939a)}

/* online study */
.study{position:absolute;top:2548px;left:0;width:1200px;height:412px;background:linear-gradient(180deg,#eeeeec 0%,#dedcd7 60%,#3a3f4a 100%)}
.study .screen{position:absolute;left:445px;top:100px;width:300px;height:170px;background:var(--white);border:10px solid #222;text-align:center;padding-top:20px}
.study .screen strong{display:block;font-size:40px;font-weight:800;color:var(--green);line-height:1}
.study .screen span{display:block;font-size:16px;font-weight:800;color:var(--green);margin-top:6px;line-height:1.2}
.study .free{position:absolute;left:345px;top:70px;width:130px;height:130px;border-radius:50%;background:var(--green);color:var(--white);font-size:28px;font-weight:800;display:flex;align-items:center;justify-content:center;border:5px solid var(--white)}
.study .cta{position:absolute;left:770px;top:180px}

/* testimonials */
.testimonials{position:absolute;top:3015px;left:0;width:1200px;text-align:center}
.testimonials blockquote{font-family:"Lora",Georgia,serif;font-style:italic;font-size:18px;color:#555;line-height:1.6;width:900px;margin:50px auto 0}
.testimonials .arrow{position:absolute;top:105px}
.testimonials .avatar{width:34px;height:34px;border-radius:50%;background:#f1d2c9;margin:40px auto 10px}
.testimonials .who{font-size:11px;font-weight:700;color:#555;text-transform:uppercase}
.testimonials .role{font-size:10px;color:#999}

/* mailing */
.mailing{position:absolute;top:3330px;left:0;width:1200px;height:64px;background:var(--green);display:flex;align-items:center;padding:0 100px;gap:120px}
.mailing h3{color:var(--white);font-size:22px;font-weight:600;text-transform:uppercase}
.mailing form{display:flex}
.mailing .field{width:300px;height:38px;background:var(--white);font-size:14px;color:#999;padding:9px 14px}
.mailing .submit{width:130px;height:38px;background:#222;color:var(--white);font-size:13px;font-weight:700;display:flex;align-items:center;justify-content:center;letter-spacing:1px}

/* contact */
.contact{position:absolute;top:3394px;left:0;width:1200px;height:546px;background:var(--navy);color:var(--white)}
.contact h3{position:absolute;left:70px;top:50px;font-size:22px;font-weight:700;text-transform:uppercase}
.contact .details{position:absolute;left:80px;top:120px;width:280px}
.detail{display:flex;gap:14px;margin-bottom:30px}
.detail .ic{width:30px;flex:none}
.detail h5{font-size:14px;font-weight:700;text-transform:uppercase}
.detail p{font-size:12px;color:#c9d3ee;line-height:1.6;margin-top:4px}
.message{position:absolute;left:430px;top:110px;width:420px}
.message h5{font-size:12px;font-weight:700;text-transform:uppercase;margin-bottom:12px}
.message .row{display:flex;gap:12px}
.message .input{flex:1;height:34px;background:#2a4c9c;border:1px solid #4a68ad;font-size:12px;color:#b6c3e4;padding:8px 10px}
.message .area{height:120px;margin-top:12px;background:#2a4c9c;border:1px solid #4a68ad;font-size:12px;color:#b6c3e4;padding:8px 10px}
.message .send{margin-top:14px;width:90px;height:32px;background:var(--blue-light);font-size:12px;font-weight:700;display:flex;align-items:center;justify-content:center}
.partner{position:absolute;left:880px;top:150px}
.partner h4{font-size:20px;font-weight:800;text-transform:uppercase;line-height:1.2}
.partner .box{margin-top:14px;width:240px;height:110px;background:#111;display:flex;align-items:center;justify-content:center;font-size:20px;font-weight:800;color:var(--white)}
.follow{position:absolute;left:170px;top:470px;display:flex;align-items:center;gap:18px}
.follow span.label{font-size:13px;font-weight:700;text-transform:uppercase}
.follow .pill{width:120px;height:32px;border-radius:16px;font-size:12px;display:flex;align-items:center;justify-content:center;gap:8px}
.pill i{width:10px;height:10px;border-radius:50%;background:var(--white);display:block}

.footer{position:absolute;top:3940px;left:0;width:1200px;height:124px;background:var(--navy-deep);color:#c9d3ee;display:flex;justify-content:space-between;align-items:center;padding:0 70px;font-size:12px}
.footer nav{display:flex;gap:30px;font-weight:700;text-transform:uppercase;color:var(--white)}
</style>
</head>
<body>

<div class="topbar">
  <div class="phone">
    <svg width="14" height="14" viewBox="0 0 24 24"><path fill="#cfd8ee" d="M6.6 10.8a15 15 0 0 0 6.6 6.6l2.2-2.2c.3-.3.7-.4 1-.2 1.1.4 2.3.6 3.6.6.6 0 1 .4 1 1V20c0 .6-.4 1-1 1A17 17 0 0 1 3 4c0-.6.4-1 1-1h3.5c.6 0 1 .4 1 1 0 1.3.2 2.5.6 3.6.1.3 0 .7-.2 1z"/></svg>
    +100 555 0142
  </div>
  <div class="dots"><span></span><span></span><span></span><span></span><span></span></div>
</div>

<header class="hero">
  <div class="hero-photo" role="img" aria-label="Bright workspace with a desktop computer, desk lamp and speakers on a wooden desk"></div>
  <nav class="nav">
    <ul><li><a href="#">Home</a></li><li><a href="#">About Us</a></li></ul>
    <ul><li><a href="#">Courses</a></li><li><a href="#">Contact Us</a></li></ul>
  </nav>
  <div class="brand">
    <div class="mark"></div>
    <div class="name">CORVALE</div>
    <div class="tag">INSTITUTE OF BUSINESS &amp; TECHNOLOGY</div>
  </div>
  <div class="hero-copy">
    <h1>Lorem ipsum dolor sit amet</h1>
    <p>Lorem ipsum dolor sit amet, consectetur adipiscing elit</p>
  </div>
  <div class="btn">LEARN MORE</div>
  <svg class="divider" width="1200" height="110" viewBox="0 0 1200 110">
    <polygon points="0,40 560,95 600,110 0,110" fill="#c7ccd6"/>
    <polygon points="1200,40 640,95 600,110 1200,110" fill="#c7ccd6"/>
    <polygon points="0,70 600,110 1200,70 1200,110 0,110" fill="#fff"/>
    <polygon points="570,70 630,70 600,100" fill="var(--navy)"/>
  </svg>
</header>

<section class="programs">
  <h2 class="section-title">Our Programs Offered</h2>
  <div class="program-list">
    <div class="program"><div class="icon"><svg width="44" height="44" viewBox="0 0 44 44"><polygon points="22,8 42,18 22,28 2,18" fill="#fff"/><rect x="12" y="24" width="20" height="10" fill="#fff"/></svg></div><h3>University Education – Long Distance Learning</h3></div>
    <div class="program"><div class="icon"><svg width="44" height="44" viewBox="0 0 44 44"><rect x="8" y="8" width="28" height="20" fill="#fff"/><rect x="16" y="30" width="12" height="6" fill="#fff"/></svg></div><h3>Modular Soft Skills</h3></div>
    <div class="program active"><div class="icon"><svg width="44" height="44" viewBox="0 0 44 44"><circle cx="22" cy="16" r="8" fill="#fff"/><rect x="10" y="26" width="24" height="12" rx="6" fill="#fff"/></svg></div><h3>Short to Diploma (DIS)</h3></div>
    <div class="program"><div class="icon"><svg width="44" height="44" viewBox="0 0 44 44"><circle cx="22" cy="18" r="10" fill="#fff"/><rect x="17" y="30" width="10" height="6" fill="#fff"/></svg></div><h3>Technology</h3></div>
    <div class="program"><div class="icon"><svg width="44" height="44" viewBox="0 0 44 44"><rect x="6" y="10" width="32" height="22" fill="#fff"/><rect x="2" y="32" width="40" height="4" fill="#fff"/></svg></div><h3>Skillbridge Online in The Talent Continuum</h3></div>
    <div class="program"><div class="icon"><svg width="44" height="44" viewBox="0 0 44 44"><rect x="6" y="14" width="32" height="22" rx="2" fill="#fff"/><rect x="16" y="8" width="12" height="6" fill="none" stroke="#fff" stroke-width="3"/></svg></div><h3>Business Portals</h3></div>
  </div>
</section>

<section class="about">
  <h2 class="section-title">About Corvale Institute of Business and Technology</h2>
  <p class="intro">Lorem ipsum dolor sit amet, consectetur adipiscing elit, sed do eiusmod tempor incididunt ut labore et dolore magna aliqua. Ut enim ad minim veniam, quis nostrud exercitation ullamco laboris nisi ut aliquip ex ea commodo consequat. Duis aute irure dolor in reprehenderit in voluptate velit esse cillum dolore eu fugiat nulla pariatur. Excepteur sint occaecat cupidatat non proident, sunt in culpa qui officia deserunt mollit anim id est laborum.</p>
  <div class="about-boxes">
    <div class="about-box"><h4><svg width="24" height="24" viewBox="0 0 24 24"><rect x="2" y="2" width="20" height="20" fill="none" stroke="var(--green)" stroke-width="2"/><path d="M6 12l4 4 8-8" fill="none" stroke="var(--green)" stroke-width="2"/></svg>What We Do</h4><p>Duis autem vel eum iriure dolor in hendrerit in vulputate velit esse molestie consequat. Nam liber tempor cum soluta nobis eleifend option congue nihil imperdiet doming id quod.</p></div>
    <div class="about-box"><h4><svg width="24" height="24" viewBox="0 0 24 24"><circle cx="12" cy="12" r="10" fill="none" stroke="var(--green)" stroke-width="2"/><circle cx="12" cy="12" r="4" fill="var(--green)"/></svg>Our Mission</h4><p>Duis autem vel eum iriure dolor in hendrerit in vulputate velit esse molestie consequat. Nam liber tempor cum soluta nobis eleifend option congue nihil imperdiet doming id quod.</p></div>
    <div class="about-box"><h4><svg width="24" height="24" viewBox="0 0 24 24"><polygon points="12,2 15,9 22,9 16,14 18,21 12,17 6,21 8,14 2,9 9,9" fill="none" stroke="var(--green)" stroke-width="2"/></svg>Company Value</h4><p>Duis autem vel eum iriure dolor in hendrerit in vulputate velit esse molestie consequat. Nam liber tempor cum soluta nobis eleifend option congue nihil imperdiet doming id quod.</p></div>
  </div>
</section>

<section class="why">
  <h2 class="section-title">Why Choose Corvale Institute of Business and Technology</h2>
  <div class="why-grid">
    <div class="why-item"><div class="num">01</div><h4>Over 50 years of experience</h4><p>Duis autem vel eum iriure dolor in hendrerit in vulputate velit esse molestie consequat. Nam liber tempor cum soluta nobis eleifend option congue.</p></div>
    <div class="why-item"><div class="num">02</div><h4>We are passionate</h4><p>Duis autem vel eum iriure dolor in hendrerit in vulputate velit esse molestie consequat. Nam liber tempor cum soluta nobis eleifend option congue.</p></div>
    <div class="why-item"><div class="num">03</div><h4>We are fast, accuracy &amp; reliable</h4><p>Duis autem vel eum iriure dolor in hendrerit in vulputate velit esse molestie consequat. Nam liber tempor cum soluta nobis eleifend option congue.</p></div>
    <div class="why-item"><div class="num">04</div><h4>We are improving everyday</h4><p>Duis autem vel eum iriure dolor in hendrerit in vulputate velit esse molestie consequat. Nam liber tempor cum soluta nobis eleifend option congue.</p></div>
  </div>
  <div class="why-photo" role="img" aria-label="Student standing in a bright modern office"></div>
</section>

<section class="study" role="img" aria-label="Desk with a computer monitor, keyboard, notebook and glasses advertising free online study resources">
  <div class="free">FREE</div>
  <div class="screen"><strong>ONLINE STUDY</strong><span>RESOURCE WHICH<br>FREE</span></div>
  <svg class="cta" width="170" height="60" viewBox="0 0 170 60"><polygon points="0,8 140,8 168,30 140,52 0,52" fill="var(--orange)"/><text x="70" y="36" text-anchor="middle" font-family="Open Sans, sans-serif" font-size="17" font-weight="800" fill="#fff">CLICK HERE</text></svg>
</section>

<section class="testimonials">
  <h2 class="section-title">Client's Testimonials</h2>
  <svg class="arrow" style="left:80px" width="24" height="50" viewBox="0 0 24 50"><path d="M22 2L2 25l20 23" fill="none" stroke="#ccc" stroke-width="2"/></svg>
  <svg class="arrow" style="right:80px" width="24" height="50" viewBox="0 0 24 50"><path d="M2 2l20 23L2 48" fill="none" stroke="#ccc" stroke-width="2"/></svg>
  <blockquote>Lorem ipsum dolor sit amet, consectetur adipiscing elit, sed do eiusmod tempor incididunt ut labore et dolore magna aliqua. Ut enim ad minim veniam, quis nostrud exercitation ullamco laboris nisi ut aliquip ex ea commodo consequat.</blockquote>
  <div class="avatar"></div>
  <div class="who">Marcus Ellery</div>
  <div class="role">Graduate Student</div>
</section>

<section class="mailing">
  <h3>Join Our Mailing List</h3>
  <form><div class="field">Sign up to our mailing list</div><div class="submit">SUBSCRIBE</div></form>
</section>

<footer class="contact">
  <h3>Get In Touch Now!</h3>
  <div class="details">
    <div class="detail"><svg class="ic" width="22" height="26" viewBox="0 0 22 26"><path d="M11 1a9 9 0 0 0-9 9c0 7 9 15 9 15s9-8 9-15a9 9 0 0 0-9-9z" fill="#fff"/><circle cx="11" cy="10" r="3" fill="var(--navy)"/></svg><div><h5>Address</h5><p>Harbourline Plaza, Westgate<br>Block 4, Suite 12<br>Riverside District</p></div></div>
    <div class="detail"><svg class="ic" width="22" height="22" viewBox="0 0 24 24"><path fill="#fff" d="M6.6 10.8a15 15 0 0 0 6.6 6.6l2.2-2.2c.3-.3.7-.4 1-.2 1.1.4 2.3.6 3.6.6.6 0 1 .4 1 1V20c0 .6-.4 1-1 1A17 17 0 0 1 3 4c0-.6.4-1 1-1h3.5c.6 0 1 .4 1 1 0 1.3.2 2.5.6 3.6.1.3 0 .7-.2 1z"/></svg><div><h5>Phone</h5><p>+100 555 0142 &nbsp;/&nbsp; +100 555 0187</p></div></div>
    <div class="detail"><svg class="ic" width="24" height="18" viewBox="0 0 24 18"><rect x="1" y="1" width="22" height="16" fill="#fff"/><path d="M1 1l11 9 11-9" fill="none" stroke="var(--navy)" stroke-width="2"/></svg><div><h5>Email</h5><p>hello@corvale-institute.test</p></div></div>
  </div>
  <div class="message">
    <h5>Leave a Message</h5>
    <div class="row"><div class="input">Name</div><div class="input">Email</div></div>
    <div class="area">Message</div>
    <div class="send">SUBMIT</div>
  </div>
  <div class="partner">
    <h4>In Conjunction<br>With Skillbridge</h4>
    <div class="box">SKILLBRIDGE</div>
  </div>
  <div class="follow">
    <span class="label">Follow Us</span>
    <div class="pill" style="background:#3b5998"><i></i>Network</div>
    <div class="pill" style="background:#3fa9e6"><i></i>Updates</div>
    <div class="pill" style="background:#d6452f"><i></i>Circles</div>
    <div class="pill" style="background:#c8232c"><i></i>Boards</div>
    <div class="pill" style="background:#1d79b3"><i></i>Careers</div>
  </div>
</footer>

<div class="footer">
  <nav><span>Home</span><span>About Us</span><span>Courses</span><span>Contact Us</span></nav>
  <span>© 2015 Corvale Institute of Business and Technology. All Rights Reserved.</span>
</div>

</body>
</html>
```